Slick Boot Gig - 20 Years of Funk

I'm with a funk band called Slick Boot. We are celebrating our 20 year anniversary with a show on August 3, 2024. We would like some banners made for social media to help promote the gig. I'm attaching some examples of our 10 year anniversary gig so you can at least get an idea of what we are looking for.

Here's the text for the banners:
SLICK BOOT Anniversary Gig - 20 Years of Funk!
Saturday, August 10, 2024
with special guest: Marco Delven
Doors at 7pm, Show at 8pm

We would like three sizes:
1920 x 1005 pixels
1080 x 1080 pixels
1080 x 1920 pixels

You can check out our website for more ideas of our graphic style, etc.. www.slickbootband.example

```html
<!DOCTYPE html>
<html lang="en">
<head>
<meta charset="utf-8">
<title>Slick Boot – 20 Years of Funk Banners</title>
<link href="https://fonts.googleapis.com/css2?family=Montserrat:wght@400;500;700;800&family=Bowlby+One&family=Lobster&display=swap" rel="stylesheet">
<style>
  :root{
    --canvas:#e4e4e4;
    --purple:#3f0d4e;
    --pink:#d83c98;
    --cyan:#10b3d6;
    --lime:#c8e02b;
    --ink:#111111;
    --white:#ffffff;
  }
  *{box-sizing:border-box;margin:0;padding:0}
  html,body{width:1200px;height:1200px;overflow:hidden}
  body{background:var(--canvas);position:relative;font-family:"Montserrat",sans-serif;color:var(--white)}

  .banner{position:absolute;overflow:hidden}
  .banner--story{left:87px;top:227px;width:352px;height:626px;
    background:
      radial-gradient(circle at 0% 0%, var(--pink) 0, transparent 38%),
      radial-gradient(circle at 100% 12%, var(--cyan) 0, transparent 42%),
      radial-gradient(circle at 0% 92%, var(--cyan) 0, transparent 45%),
      radial-gradient(circle at 100% 100%, var(--pink) 0, transparent 42%),
      var(--purple);}
  .banner--wide{left:487px;top:227px;width:626px;height:327px;
    background:
      radial-gradient(circle at 40% 0%, var(--cyan) 0, transparent 32%),
      radial-gradient(circle at 0% 30%, var(--pink) 0, transparent 35%),
      radial-gradient(circle at 0% 100%, var(--cyan) 0, transparent 35%),
      radial-gradient(circle at 100% 75%, var(--pink) 0, transparent 40%),
      var(--purple);}
  .banner--square{left:487px;top:620px;width:352px;height:352px;
    background:
      radial-gradient(circle at 0% 0%, var(--pink) 0, transparent 40%),
      radial-gradient(circle at 100% 0%, var(--cyan) 0, transparent 40%),
      radial-gradient(circle at 0% 100%, var(--cyan) 0, transparent 45%),
      radial-gradient(circle at 100% 100%, var(--pink) 0, transparent 45%),
      var(--purple);}

  .photo{position:absolute;
    background:linear-gradient(160deg,#c9c0cc 0%,#f07cc0 40%,#f6d8ec 62%,#8fd8ea 85%,#4c3a5a 100%);
    -webkit-mask-image:linear-gradient(to bottom,#000 70%,transparent 100%);
    mask-image:linear-gradient(to bottom,#000 70%,transparent 100%);}
  .banner--story .photo{left:29px;top:40px;width:295px;height:237px}
  .banner--wide .photo{left:0;top:33px;width:328px;height:294px;
    -webkit-mask-image:linear-gradient(to right,#000 75%,transparent 100%);
    mask-image:linear-gradient(to right,#000 75%,transparent 100%);}
  .banner--square .photo{left:38px;top:14px;width:292px;height:182px}

  .band-name{position:absolute;font-weight:800;color:var(--lime);white-space:nowrap;text-align:center}
  .banner--story .band-name{left:0;width:352px;top:272px;font-size:40px}
  .banner--wide .band-name{left:337px;width:257px;top:30px;font-size:40px}

  .badge{position:absolute;left:21px;top:206px;width:91px;height:91px;border-radius:50%;
    background:var(--ink);border:6px solid var(--lime);
    display:flex;align-items:center;justify-content:center}
  .badge__name{font-weight:800;font-size:15px;color:var(--lime);white-space:nowrap}

  .promo{position:absolute;width:284px;height:222px;transform-origin:top left}
  .banner--story .promo{left:34px;top:362px}
  .banner--wide .promo{left:337px;top:96px;transform:scale(0.91)}
  .banner--square .promo{left:125px;top:166px;transform:scale(0.715)}

  .promo__tag{position:absolute;top:0;left:0;width:100%;text-align:center;font-weight:700;font-size:17px;letter-spacing:.3px}
  .headline{position:absolute;top:22px;left:0;width:284px;height:100px}
  .headline__num{position:absolute;left:0;top:18px;font-family:"Bowlby One",sans-serif;font-size:58px;line-height:1;color:var(--lime);text-shadow:3px 3px 0 var(--ink)}
  .headline__word{position:absolute;left:104px;top:-6px;font-family:"Lobster",cursive;font-size:78px;line-height:1;color:var(--lime);text-shadow:3px 3px 0 var(--ink)}
  .headline__sub{position:absolute;left:150px;top:80px;font-weight:800;font-style:italic;font-size:12px;color:var(--ink);background:var(--lime);padding:0 8px;border-radius:2px}

  .details{position:absolute;top:126px;left:0;width:284px;height:62px;display:flex;align-items:center}
  .details__date{width:118px;line-height:1}
  .details__day{display:block;font-size:13px;font-weight:500;margin-bottom:3px}
  .details__when{display:block;font-size:18px;font-weight:800;color:var(--lime);line-height:.95}
  .details__label{border-left:2px solid var(--white);padding-left:10px;height:60px;font-size:15px;line-height:1.3;width:95px;display:flex;align-items:center}
  .details__guest{font-size:25px;font-weight:800;color:var(--lime);line-height:1.15}

  .doors{position:absolute;top:194px;left:0;width:284px;height:30px;border:2px solid var(--white);
    display:flex;align-items:center;justify-content:center;font-size:16px;font-weight:500;white-space:nowrap}
  .doors strong{color:var(--lime);font-weight:800}
</style>
</head>
<body>

<section class="banner banner--story">
  <div class="photo" role="img" aria-label="Band singers performing at a microphone, tinted pink and blue"></div>
  <div class="band-name">Slick Boot</div>
  <div class="promo">
    <div class="promo__tag">ANNIVERSARY GIG</div>
    <div class="headline"><span class="headline__num">20</span><span class="headline__word">Years</span><span class="headline__sub">OF FUNK!</span></div>
    <div class="details">
      <div class="details__date"><span class="details__day">SATURDAY,</span><span class="details__when">AUGUST<br>10, 2024</span></div>
      <div class="details__label">With<br>Special<br>Guest:</div>
      <div class="details__guest">Marco<br>Delven</div>
    </div>
    <div class="doors">Doors at&nbsp;<strong>7pm, SHOW</strong>&nbsp;at&nbsp;<strong>8pm</strong></div>
  </div>
</section>

<section class="banner banner--wide">
  <div class="photo" role="img" aria-label="Band singers performing at a microphone, tinted pink and blue"></div>
  <div class="band-name">Slick Boot</div>
  <div class="promo">
    <div class="promo__tag">ANNIVERSARY GIG</div>
    <div class="headline"><span class="headline__num">20</span><span class="headline__word">Years</span><span class="headline__sub">OF FUNK!</span></div>
    <div class="details">
      <div class="details__date"><span class="details__day">SATURDAY,</span><span class="details__when">AUGUST<br>10, 2024</span></div>
      <div class="details__label">With<br>Special<br>Guest:</div>
      <div class="details__guest">Marco<br>Delven</div>
    </div>
    <div class="doors">Doors at&nbsp;<strong>7pm, SHOW</strong>&nbsp;at&nbsp;<strong>8pm</strong></div>
  </div>
</section>

<section class="banner banner--square">
  <div class="photo" role="img" aria-label="Band singers performing at a microphone, tinted pink and blue"></div>
  <div class="badge"><span class="badge__name">Slick Boot</span></div>
  <div class="promo">
    <div class="promo__tag">ANNIVERSARY GIG</div>
    <div class="headline"><span class="headline__num">20</span><span class="headline__word">Years</span><span class="headline__sub">OF FUNK!</span></div>
    <div class="details">
      <div class="details__date"><span class="details__day">SATURDAY,</span><span class="details__when">AUGUST<br>10, 2024</span></div>
      <div class="details__label">With<br>Special<br>Guest:</div>
      <div class="details__guest">Marco<br>Delven</div>
    </div>
    <div class="doors">Doors at&nbsp;<strong>7pm, SHOW</strong>&nbsp;at&nbsp;<strong>8pm</strong></div>
  </div>
</section>

</body>
</html>
```